Stylish Business Cards Wanted

- DOUBLE SIDED Design Required -

High end, edgy cards for a corporate and personal stylist. Must include logo,
Name: Belinda Harwick
Title: Director and Stylist
telephone : +61 8 7142 5809
email: belinda@theloombriefing.example
website: theloombriefing.example
Tag: Corporate Workwear & Uniform Specialist | Personal Stylist
Would like nice icons for telephone, email, website

Target Market(s)

Businesses wanting stylish uniforms, people wanting stylish wardrobes

Industry/Entity Type

Corporate Workwear Stylist

Contact Information for Business Card

I would like black, white and gold foiling incorporated in the design - possibly a touch of the other colours on my branding guide attached Name: Belinda Harwick Title: Director and Stylist telephone : +61 8 7142 5809 email: belinda@theloombriefing.example website: theloombriefing.example Tag: Corporate Workwear & Uniform Specialist | Personal Stylist Would like nice icons for telephone, email, website

Font styles to use
Other font styles liked:
• Raleway

Colors

Designer to choose colors to be used in the design.

Requirements
Must have
• Gold foil accents

```html
<!DOCTYPE html>
<html lang="en">
<head>
<meta charset="utf-8">
<title>The Loom Briefing — Business Cards</title>
<link href="https://fonts.googleapis.com/css2?family=Raleway:wght@400;500;600;700&family=Satisfy&display=swap" rel="stylesheet">
<style>
  :root {
    --backdrop: #3b3b3d;
    --card-black: #232325;
    --gold: #e1b64f;
    --white: #ffffff;
  }
  * { box-sizing: border-box; margin: 0; padding: 0; }
  html, body {
    width: 799px; height: 1200px; overflow: hidden;
    background: var(--backdrop);
  }
  .sheet {
    position: relative; width: 799px; height: 1200px;
    display: flex; flex-direction: column; align-items: center; justify-content: center; gap: 120px;
  }
  .card {
    position: relative; width: 680px; height: 390px;
    background: var(--card-black); border-radius: 26px; overflow: hidden;
    box-shadow: 0 14px 30px rgba(0,0,0,.45);
  }
  .card--front { display: flex; align-items: center; justify-content: center; }
  .brand-name {
    font-family: "Raleway", sans-serif; font-weight: 600;
    color: var(--gold); letter-spacing: 2px; text-align: center; line-height: 1.05;
  }
  .card--front .brand-name { font-size: 58px; }
  .wave { position: absolute; inset: 0; width: 100%; height: 100%; }
  .holder { position: absolute; left: 40px; top: 112px; }
  .holder__name {
    font-family: "Satisfy", cursive; color: var(--gold); font-size: 36px; line-height: 1.1;
  }
  .holder__title {
    font-family: "Raleway", sans-serif; color: var(--white); font-size: 15px; margin-top: 4px;
  }
  .contacts { position: absolute; left: 40px; top: 200px; list-style: none; }
  .contacts li {
    display: flex; align-items: center; gap: 10px;
    font-family: "Raleway", sans-serif; font-size: 16px; color: var(--white);
    margin-bottom: 9px; white-space: nowrap;
  }
  .contacts svg { width: 16px; height: 16px; flex: none; }
  .social-box { width: 16px; height: 16px; background: var(--gold); border-radius: 3px; flex: none; }
  .tagline {
    position: absolute; right: 34px; top: 100px; text-align: right;
    font-family: "Satisfy", cursive; font-size: 16px; line-height: 1.35; color: var(--card-black);
  }
  .card--back .brand-name {
    position: absolute; right: 40px; bottom: 30px; font-size: 36px; color: var(--white);
  }
</style>
</head>
<body>
<main class="sheet">

  <section class="card card--front" aria-label="Card front">
    <p class="brand-name">The Loom<br>Briefing</p>
  </section>

  <section class="card card--back" aria-label="Card back">
    <svg class="wave" viewBox="0 0 680 390" preserveAspectRatio="none" aria-hidden="true">
      <path d="M0,0 H680 V270 C600,266 530,245 480,208 C410,150 320,58 0,28 Z" fill="var(--gold)"/>
      <path d="M30,40 C180,42 320,78 430,150" fill="none" stroke="var(--card-black)" stroke-width="7" stroke-linecap="round"/>
      <path d="M80,30 C210,32 310,56 390,100" fill="none" stroke="var(--card-black)" stroke-width="3" stroke-linecap="round"/>
    </svg>

    <div class="holder">
      <p class="holder__name">Belinda Harwick</p>
      <p class="holder__title">Director and Stylist</p>
    </div>

    <ul class="contacts">
      <li><span class="social-box"></span>/theloombriefing101</li>
      <li>
        <svg viewBox="0 0 16 16"><path d="M4 2l2 3-1.3 1.3c.8 1.8 2.2 3.2 4 4L10 9l3 2-1 2.5c-5 0-10-5-10-10z" fill="none" stroke="var(--gold)" stroke-width="1.3"/></svg>
        +61 8 7142 5809
      </li>
      <li>
        <svg viewBox="0 0 16 16"><rect x="1.5" y="3.5" width="13" height="9" fill="none" stroke="var(--gold)" stroke-width="1.3"/><path d="M1.5 3.5l6.5 5 6.5-5" fill="none" stroke="var(--gold)" stroke-width="1.3"/></svg>
        belinda@theloombriefing.example
      </li>
      <li>
        <svg viewBox="0 0 16 16"><circle cx="8" cy="8" r="6.5" fill="none" stroke="var(--gold)" stroke-width="1.3"/><path d="M1.5 8h13M8 1.5c-3 3.5-3 9.5 0 13M8 1.5c3 3.5 3 9.5 0 13" fill="none" stroke="var(--gold)" stroke-width="1.1"/></svg>
        theloombriefing.example
      </li>
    </ul>

    <p class="tagline">Corporate Workwear «<br>and Uniform Specialist «<br>Personal Stylist «</p>

    <p class="brand-name">The Loom<br>Briefing</p>
  </section>

</main>
</body>
</html>
```